Open sky harmony Business cards - yoga studio

We need business cards for our yoga studio Opensky Harmony.
We would like to see designs that include the colour blue and our logo.
The business card should communicate a feeling of strength and calm

Requirements
Must have
• The business card must include
"Mirela Thornquist - Director"
and
"42 Wattlecrest Avenue
Dunmoreton
VIC 3917
Ph - 0471 586 204"

```html
<!DOCTYPE html>
<html lang="en">
<head>
<meta charset="utf-8">
<title>Opensky Harmony – Business Cards</title>
<link href="https://fonts.googleapis.com/css2?family=Open+Sans:wght@300;400;700&display=swap" rel="stylesheet">
<style>
  :root {
    --backdrop: #ecebe9;
    --card: #ffffff;
    --teal: #4aa6b3;
    --ink: #1c1c1c;
    --shadow: rgba(0, 0, 0, 0.12);
  }
  * { box-sizing: border-box; margin: 0; padding: 0; }
  html, body {
    width: 1200px;
    height: 997px;
    overflow: hidden;
    background: var(--backdrop);
    font-family: "Open Sans", Arial, sans-serif;
  }
  .card-set {
    position: relative;
    width: 1200px;
    height: 997px;
    display: flex;
    align-items: center;
    justify-content: center;
    gap: 60px;
  }
  .card {
    width: 520px;
    height: 297px;
    background: var(--card);
    box-shadow: 0 6px 18px var(--shadow);
    display: flex;
    flex-direction: column;
    align-items: center;
    justify-content: center;
    text-align: center;
  }
  /* Front */
  .brand {
    display: flex;
    align-items: center;
    gap: 16px;
  }
  .brand-dot {
    width: 44px;
    height: 44px;
    border-radius: 50%;
    background: var(--teal);
  }
  .brand-name {
    color: var(--teal);
    font-weight: 300;
    font-size: 40px;
    letter-spacing: 0.5px;
  }
  /* Back */
  .mark-dot {
    width: 38px;
    height: 38px;
    border-radius: 50%;
    background: var(--teal);
    margin-bottom: 12px;
  }
  .person-name {
    color: var(--ink);
    font-weight: 700;
    font-size: 17px;
  }
  .person-role {
    color: var(--teal);
    font-size: 14px;
    margin-top: 2px;
  }
  .divider {
    width: 150px;
    height: 1px;
    background: var(--teal);
    margin: 10px 0 12px;
  }
  .contact {
    color: var(--ink);
    font-size: 15px;
    line-height: 1.35;
    font-style: normal;
  }
</style>
</head>
<body>
  <main class="card-set">
    <section class="card card-front" aria-label="Card front">
      <div class="brand">
        <span class="brand-dot" aria-hidden="true"></span>
        <span class="brand-name">Opensky Harmony</span>
      </div>
    </section>
    <section class="card card-back" aria-label="Card back">
      <span class="mark-dot" aria-hidden="true"></span>
      <p class="person-name">Mirela Thornquist</p>
      <p class="person-role">Director</p>
      <span class="divider" aria-hidden="true"></span>
      <address class="contact">
        42 Wattlecrest Avenue<br>
        Dunmoreton, VIC 3917<br>
        ph 0471 586 204
      </address>
    </section>
  </main>
</body>
</html>
```